Human Resource Consulting practice needs a business card design

We need a business card design (double sided colour) for our Human Resource (HR) consulting practice in regional New South Wales, australia. Our business name is Staff Compass. We support small and medium business across the Mid North Coast of New South Wales by providing them with outsourced HR support, services and products to help them achieve compliance with workplace legislation and across all areas of the employment lifecycle from recruitment to termination and everything in between. Our corporate colours are hot pink and black. The final design should communicate professionalism, trust, people focus.
I have attached the current (old) business card for your reference.

Target Market(s)

Business owners and high level managers

Industry/Entity Type

Business

Contact Information for Business Card

Name
Title
Phone no
Mobile no
Address
PO Box
email address
website

Colors
e34197

Requirements
Must have
• Tempate for changing business card personal details including Name, position title, mobile number, email address.
• Keep current logo and colours as per attached
• Logo must be presented in 2 colours or black only not white
Nice to have
• One side logo and graphic only other side logo and personal details
Should not have
• Should not be the same as the current version (attached) but a modern interpretation.
• Does not need a busy reverse side with our list of services as per current version. I feel this is too busy.
• No photos

```html
<!DOCTYPE html>
<html lang="en">
<head>
<meta charset="utf-8">
<title>Staff Compass – Business Card</title>
<link rel="stylesheet" href="https://fonts.googleapis.com/css2?family=Michroma&family=Arimo:wght@400;700&display=swap">
<style>
  :root {
    --hot-pink: #e31cae;
    --pink-light: #f04fc8;
    --pink-deep: #c9139a;
    --black: #0b0b0b;
    --ink: #151515;
    --white: #ffffff;
    --grey-text: #d9d9d9;
    --backdrop: #efe9e2;
  }
  * { margin: 0; padding: 0; box-sizing: border-box; }
  html, body { width: 1200px; height: 892px; overflow: hidden; }
  body {
    background: var(--backdrop);
    display: flex;
    align-items: center;
    justify-content: center;
    gap: 80px;
    font-family: "Michroma", Arial, sans-serif;
  }
  .card {
    position: relative;
    width: 340px;
    height: 560px;
    border-radius: 22px;
    overflow: hidden;
    box-shadow: 0 14px 34px rgba(0,0,0,0.22);
  }
  .band { position: absolute; left: 0; right: 0; }

  /* Front: logo and personal details */
  .card--front { background: var(--black); }
  .band--top { top: 0; height: 52px; background: linear-gradient(180deg, var(--pink-light), var(--hot-pink)); }
  .band--bottom { bottom: 0; height: 96px; background: linear-gradient(180deg, var(--hot-pink), var(--pink-deep)); }

  .brand {
    position: absolute;
    left: 40px; top: 112px;
    display: flex; align-items: center; gap: 10px;
    color: var(--hot-pink);
    font-size: 24px;
    line-height: 1.15;
  }
  .brand__mark { width: 12px; height: 12px; background: var(--hot-pink); flex: none; }

  .person { position: absolute; left: 40px; top: 232px; }
  .person__name {
    font-weight: 400;
    color: var(--hot-pink);
    font-size: 25px;
    letter-spacing: 1px;
    white-space: nowrap;
  }
  .person__title {
    margin-top: 6px;
    color: var(--grey-text);
    font-size: 9.5px;
    letter-spacing: 1.2px;
  }

  .contacts { position: absolute; left: 40px; top: 312px; list-style: none; }
  .contacts li {
    display: flex; align-items: center; gap: 10px;
    color: var(--white);
    font-size: 11.5px;
    height: 20px;
    white-space: nowrap;
  }
  .icon {
    width: 14px; height: 14px; border-radius: 3px;
    background: var(--hot-pink); flex: none;
    display: flex; align-items: center; justify-content: center;
  }
  .address {
    position: absolute; left: 40px; top: 420px;
    color: var(--white);
    font-size: 11px;
    line-height: 1.55;
  }

  /* Back: logo and line only */
  .card--back { background: linear-gradient(160deg, var(--pink-light) 0%, var(--hot-pink) 55%, var(--pink-deep) 100%); }
  .band--bottom-black { bottom: 0; height: 104px; background: var(--ink); }
  .back-brand {
    position: absolute; left: 0; right: 0; top: 190px;
    display: flex; align-items: center; justify-content: center; gap: 12px;
    color: var(--black);
    font-size: 26px;
    white-space: nowrap;
  }
  .back-brand__mark { width: 13px; height: 13px; background: var(--black); flex: none; }
  .tagline {
    position: absolute; left: 30px; right: 30px; top: 256px;
    text-align: center;
    font-family: "Arimo", Arial, sans-serif;
    font-weight: 700;
    color: var(--white);
    font-size: 15px;
    line-height: 1.4;
  }
</style>
</head>
<body>

  <section class="card card--front" aria-label="Card front">
    <div class="band band--top"></div>

    <div class="brand"><span class="brand__mark"></span><span>Staff<br>Compass</span></div>

    <div class="person">
      <h1 class="person__name">Maren Tolley</h1>
      <p class="person__title">PRINCIPAL CONSULTANT</p>
    </div>

    <ul class="contacts">
      <li><span class="icon"><svg width="9" height="9" viewBox="0 0 10 10"><path d="M2 1h2l1 2-1.2 1a5 5 0 0 0 2.2 2.2L7 5l2 1v2a1 1 0 0 1-1 1A8 8 0 0 1 1 2a1 1 0 0 1 1-1z" fill="#fff"/></svg></span>02 5550 1842</li>
      <li><span class="icon"><svg width="9" height="9" viewBox="0 0 10 10"><rect x="2.5" y="0.5" width="5" height="9" rx="1" fill="#fff"/><rect x="3.5" y="1.8" width="3" height="5.2" fill="#e31cae"/></svg></span>0400 555 316</li>
      <li><span class="icon"><svg width="9" height="9" viewBox="0 0 10 10"><rect x="1" y="4" width="8" height="5" rx="1" fill="#fff"/><rect x="3" y="1" width="4" height="3" fill="#fff"/></svg></span>02 5550 1843</li>
      <li><span class="icon"><svg width="9" height="9" viewBox="0 0 10 10"><circle cx="5" cy="5" r="4" fill="none" stroke="#fff" stroke-width="1.2"/><path d="M1 5h8M5 1v8" stroke="#fff" stroke-width="0.9"/></svg></span>www.staffcompass.com.au</li>
      <li><span class="icon"><svg width="9" height="9" viewBox="0 0 10 10"><rect x="1" y="2" width="8" height="6" fill="#fff"/><path d="M1 2l4 3.5L9 2" fill="none" stroke="#e31cae" stroke-width="1"/></svg></span>maren@staffcompass.com.au</li>
    </ul>

    <p class="address">PO Box 218, Harbour Vale,<br>NSW 2999</p>

    <div class="band band--bottom"></div>
  </section>

  <section class="card card--back" aria-label="Card back">
    <div class="back-brand"><span class="back-brand__mark"></span><span>Staff Compass</span></div>
    <p class="tagline">Building Exciting, Engaging<br>&amp; Productive Workplaces</p>
    <div class="band band--bottom-black"></div>
  </section>

</body>
</html>
```